Need Business Card for our Real Estate Business with Sales Executive's Picture

PANTONE 484 C ( RED)

PANTONE 2766 C ( BLUE

Industry/Entity Type

Real Estate

Contact Information for Business Card

Name, Mobile, email, & picture of Person
Agency Phone, address, Web address

Requirements
Must have
• Our Logo Colours, Agent Picture,

```html
<!DOCTYPE html>
<html lang="en">
<head>
<meta charset="utf-8">
<title>Meridian Business Card</title>
<link rel="stylesheet" href="https://fonts.googleapis.com/css2?family=Roboto+Condensed:wght@400;700&family=Roboto:wght@400&display=swap">
<style>
  :root {
    --navy: #0b1538;
    --red: #6e0b14;
    --grey-text: #55565a;
    --card-white: #f6f6f6;
    --stage: #e4e4e4;
    --white: #ffffff;
  }
  * { margin: 0; padding: 0; box-sizing: border-box; }
  html, body { width: 1200px; height: 960px; overflow: hidden; }
  body {
    background: var(--stage);
    position: relative;
    font-family: "Roboto", Arial, sans-serif;
  }
  .card {
    position: absolute;
    width: 600px;
    height: 343px;
    box-shadow: 0 2px 5px rgba(0,0,0,0.25);
    overflow: hidden;
  }
  .card-front { left: 314px; top: 113px; background: var(--card-white); }
  .card-back { left: 311px; top: 472px; background: var(--navy); }

  .brand {
    position: absolute;
    display: flex;
    align-items: center;
    gap: 10px;
    font-family: "Roboto Condensed", Arial, sans-serif;
    font-weight: 700;
    letter-spacing: 3px;
  }
  .brand-square { width: 12px; height: 12px; background: var(--red); }
  .card-front .brand { left: 62px; top: 176px; font-size: 42px; color: var(--navy); }
  .card-back .brand { left: 42px; top: 222px; font-size: 42px; color: var(--white); }

  .divider {
    position: absolute; left: 324px; top: 82px;
    width: 1px; height: 186px; background: #c9c9c9;
  }
  .contact { position: absolute; left: 353px; top: 80px; }
  .person-name {
    font-family: "Roboto Condensed", Arial, sans-serif;
    font-weight: 700; font-size: 21px; color: var(--navy); line-height: 26px;
  }
  .person-title {
    font-family: "Roboto Condensed", Arial, sans-serif;
    font-size: 15px; color: var(--red); line-height: 20px; margin-bottom: 8px;
  }
  .address { font-size: 14px; color: var(--grey-text); line-height: 19px; margin-bottom: 9px; }
  .contact-list { list-style: none; }
  .contact-list li {
    display: flex; align-items: center; gap: 8px;
    font-size: 14px; color: var(--grey-text); line-height: 19px;
  }
  .contact-list svg { width: 14px; height: 14px; fill: var(--navy); flex: none; }

  .stripe-navy {
    position: absolute; left: 0; bottom: 0; width: 392px; height: 12px;
    background: var(--navy);
  }
  .stripe-red {
    position: absolute; right: 0; bottom: 0; width: 208px; height: 12px;
    background: var(--red);
    clip-path: polygon(4px 0, 100% 0, 100% 100%, 0 100%);
  }

  .website {
    position: absolute; left: 42px; top: 292px; width: 230px; text-align: center;
    color: var(--white); font-size: 14px; letter-spacing: 4px;
  }
  .agent-photo {
    position: absolute; left: 341px; top: 18px; width: 250px; height: 325px;
    background: linear-gradient(180deg, #2a3566 0%, #1f3a8a 55%, #17306e 100%);
    border-radius: 110px 110px 0 0;
  }
</style>
</head>
<body>
  <section class="card card-front">
    <div class="brand"><span class="brand-square"></span>MERIDIAN</div>
    <div class="divider"></div>
    <div class="contact">
      <div class="person-name">DANIEL REYES</div>
      <div class="person-title">CEO/FOUNDER</div>
      <div class="address">4120 Willow Creek Road<br>Fairbanks, Alaska 99701</div>
      <ul class="contact-list">
        <li><svg viewBox="0 0 24 24"><path d="M6.6 10.8a15 15 0 0 0 6.6 6.6l2.2-2.2c.3-.3.7-.4 1-.2 1.1.4 2.3.6 3.6.6.6 0 1 .4 1 1V20c0 .6-.4 1-1 1A17 17 0 0 1 3 4c0-.6.4-1 1-1h3.5c.6 0 1 .4 1 1 0 1.3.2 2.5.6 3.6.1.3 0 .7-.2 1z"/></svg>555 210 4817</li>
        <li><svg viewBox="0 0 24 24"><path d="M7 1h10a2 2 0 0 1 2 2v18a2 2 0 0 1-2 2H7a2 2 0 0 1-2-2V3a2 2 0 0 1 2-2zm0 3v14h10V4zm5 15.5a1 1 0 1 0 0 2 1 1 0 0 0 0-2z"/></svg>555 382 6094</li>
        <li><svg viewBox="0 0 24 24"><path d="M2 5h20v14H2zm2 2v.5l8 5 8-5V7zm0 2.8V17h16V9.8l-8 5z"/></svg>daniel@meridian.com</li>
        <li><svg viewBox="0 0 24 24"><path d="M12 2a10 10 0 1 0 0 20 10 10 0 0 0 0-20zm-1 17.9A8 8 0 0 1 4.2 10.2L9 15v1a2 2 0 0 0 2 2zm6.9-2.5A2 2 0 0 0 16 16h-1v-3a1 1 0 0 0-1-1H8v-2h2a1 1 0 0 0 1-1V7h2a2 2 0 0 0 2-2v-.4a8 8 0 0 1 2.9 12.8z"/></svg>www.meridian.com</li>
      </ul>
    </div>
    <div class="stripe-navy"></div>
    <div class="stripe-red"></div>
  </section>

  <section class="card card-back">
    <div class="brand"><span class="brand-square"></span>MERIDIAN</div>
    <div class="website">www.meridian.com</div>
    <div class="agent-photo" role="img" aria-label="Portrait photo of the sales executive in a blue suit and striped tie"></div>
  </section>
</body>
</html>
```